Tailored Home Builders Business Card Design

We need a business card for an established builder of high quality bespoke homes in Auckland and Northland. We build and renovate homes collaboratively facilitating effective communication between owners, builders, architects, suppliers and tradespeople. We have never built or renovated a home that leaks or has faults. We only use reliable materials. We have never been sued or had legal action taken against us. We are honest builders of bespoke homes not group mass produced homes. Our niche market is in character homes. We practice sustainability and have built a lot of coastal property. We have been in business for over thirty years . We would like to see natural colors of the environment sand,sea and maybe vegetation . The design should communicate quality, sustainability,fair pricing, open communication and the originality of bespoke building. And the fact that the builder is registered.

Industry/Entity Type

Business

Contact Information for Business Card

Rowan Tellick Builders
Ph. 021583917
18 Kestrel Rd Harwood Bay Auckland 0814
PO Box 927 Mangawhai 0583

```html
<!DOCTYPE html>
<html lang="en">
<head>
<meta charset="utf-8">
<title>Tailored Home Builders – Business Card</title>
<link rel="stylesheet" href="https://fonts.googleapis.com/css2?family=Open+Sans:wght@400;600;700&display=swap">
<style>
  :root {
    --backdrop: #d9dadc;
    --card: #ffffff;
    --ink: #1e1e1e;
    --charcoal: #4a4a4a;
    --brick: #b5121b;
    --brick-soft: #d9555b;
  }
  * { box-sizing: border-box; margin: 0; padding: 0; }
  html, body { width: 1200px; height: 864px; overflow: hidden; }
  body {
    background: var(--backdrop);
    font-family: "Open Sans", Arial, sans-serif;
    position: relative;
  }
  .card {
    position: absolute;
    left: 276px;
    width: 648px;
    height: 370px;
    background: var(--card);
    box-shadow: 0 2px 8px rgba(0,0,0,.12);
    overflow: hidden;
  }
  .card--front { top: 48px; }
  .card--back { top: 446px; }

  .wordmark {
    display: flex;
    align-items: center;
    gap: 12px;
    font-weight: 700;
    color: var(--charcoal);
    white-space: nowrap;
  }
  .wordmark__dot {
    width: 14px; height: 14px;
    background: var(--brick);
    flex: none;
  }
  .card--front .wordmark {
    position: absolute;
    left: 50%; top: 50%;
    transform: translate(-50%, -50%);
    font-size: 40px;
  }
  .card--back .wordmark {
    position: absolute;
    left: 36px; top: 28px;
    font-size: 26px;
    gap: 9px;
  }
  .card--back .wordmark__dot { width: 10px; height: 10px; }

  .contact {
    position: absolute;
    left: 48px; top: 142px;
    color: var(--ink);
  }
  .contact__name {
    font-size: 19px;
    font-weight: 600;
    color: var(--brick);
    margin-bottom: 10px;
  }
  .contact__phone {
    display: flex;
    align-items: center;
    gap: 8px;
    font-size: 15px;
    margin-bottom: 18px;
  }
  .contact__phone svg { width: 12px; height: 12px; fill: var(--brick); }
  .contact__address {
    font-style: normal;
    font-size: 15px;
    line-height: 1.35;
  }
  .corner-motif {
    position: absolute;
    right: 0; bottom: 0;
    width: 330px; height: 140px;
    background: linear-gradient(135deg, rgba(255,255,255,0) 0%, var(--brick-soft) 55%, var(--brick) 100%);
    opacity: .85;
  }
</style>
</head>
<body>
  <section class="card card--front" aria-label="Card front">
    <div class="wordmark">
      <span class="wordmark__dot"></span>
      <span class="wordmark__name">Tailored Home Builders</span>
    </div>
  </section>

  <section class="card card--back" aria-label="Card back">
    <div class="wordmark">
      <span class="wordmark__dot"></span>
      <span class="wordmark__name">Tailored Home Builders</span>
    </div>

    <div class="contact">
      <p class="contact__name">Rowan Tellick Builders</p>
      <p class="contact__phone">
        <svg viewBox="0 0 24 24" aria-hidden="true"><path d="M6.6 10.8a15.1 15.1 0 0 0 6.6 6.6l2.2-2.2a1 1 0 0 1 1-.25 11.4 11.4 0 0 0 3.6.57 1 1 0 0 1 1 1V20a1 1 0 0 1-1 1A17 17 0 0 1 3 4a1 1 0 0 1 1-1h3.5a1 1 0 0 1 1 1c0 1.25.2 2.45.57 3.57a1 1 0 0 1-.25 1z"/></svg>
        021583917
      </p>
      <address class="contact__address">
        18 Kestrel Rd Harwood Bay<br>
        Auckland 0814<br>
        PO Box 927 Mangawhai 0583
      </address>
    </div>

    <div class="corner-motif" role="img" aria-label="Decorative red roofline motif area"></div>
  </section>
</body>
</html>
```